Lanternfield Drinks business cards

We need a business card design for our new logo. The company is modern, progressive, professional, yet approachable. The key products are ready to drink bottles and cans of coffee based beverages.
These cards will be a critical part of the first impression made by our sales organization, business development team, and all external facing personnel.
Card can be a vertical or horizontal orientation.

Target Market(s)

Customers, suppliers, business partners

Industry/Entity Type

Business

Contact Information for Business Card

Business cards should feature Company Name and Logo.

Font styles to use
Serif

Colors

Designer to choose colors to be used in the design.

Requirements
Must have
• Strong readability of Name, phone #, mobile number and email address.
• Job title, website url, Street Address, and other details can be secondary level readability.
Nice to have
• High impact, simplistic quality design.
• Ok to utilize the 'H in the box' separate from the company name

```html
<!DOCTYPE html>
<html lang="en">
<head>
<meta charset="utf-8">
<title>Lanternfield Drinks Business Cards</title>
<link href="https://fonts.googleapis.com/css2?family=Crimson+Pro:wght@400;600;700&display=swap" rel="stylesheet">
<style>
  :root {
    --stage: #3b3b3d;
    --card: #1e1e20;
    --card-front: #1b1b1d;
    --emboss: #58585c;
    --emboss-light: #8a8a8f;
    --orange: #e05a33;
    --amber: #ef9a2e;
    --white: #ffffff;
  }
  * { margin: 0; padding: 0; box-sizing: border-box; }
  html, body { width: 799px; height: 1200px; overflow: hidden; }
  body {
    background: var(--stage);
    font-family: "Crimson Pro", Georgia, serif;
    position: relative;
  }
  .card {
    position: absolute;
    left: 90px;
    width: 620px;
    height: 354px;
    overflow: hidden;
  }
  .card--front { top: 150px; background: var(--card-front); }
  .card--back { top: 700px; background: var(--card); }

  /* front */
  .front-mark {
    position: absolute;
    left: 50%; top: 50%;
    transform: translate(-50%, -50%);
    display: flex; flex-direction: column; align-items: center; gap: 18px;
  }
  .front-mark__square {
    width: 120px; height: 120px;
    border: 8px solid var(--emboss);
  }
  .front-mark__name {
    font-size: 26px; font-weight: 600; letter-spacing: 4px;
    color: var(--emboss-light);
    text-transform: uppercase;
  }

  /* back */
  .brand {
    position: absolute; left: 40px; top: 30px;
    display: flex; flex-direction: column; align-items: center;
    color: var(--orange); font-weight: 700;
  }
  .brand__square {
    width: 66px; height: 66px;
    border: 6px solid var(--orange);
    margin-bottom: 10px;
  }
  .brand__name { font-size: 38px; line-height: 1; letter-spacing: 1px; }
  .brand__sub { font-size: 15px; letter-spacing: 5px; margin-top: 4px; }

  .person {
    position: absolute; right: 40px; top: 120px; text-align: right;
  }
  .person__name { color: var(--orange); font-size: 26px; font-weight: 700; line-height: 1.1; }
  .person__title { color: var(--white); font-size: 16px; }

  .wave { position: absolute; left: 0; top: 0; }

  .contact {
    position: absolute; right: 24px; top: 240px;
    list-style: none; color: var(--white); font-size: 16px; line-height: 24px;
  }
  .contact__item { display: flex; justify-content: flex-end; align-items: center; gap: 10px; }
  .contact__icon { width: 15px; height: 15px; flex: none; }
</style>
</head>
<body>

<section class="card card--front" aria-label="Card front">
  <div class="front-mark">
    <div class="front-mark__square"></div>
    <div class="front-mark__name">Lanternfield Drinks</div>
  </div>
</section>

<section class="card card--back" aria-label="Card back">
  <svg class="wave" width="620" height="354" viewBox="0 0 620 354">
    <path d="M0 210 C120 200 230 250 340 244 S540 214 620 246 L620 354 L0 354 Z" fill="var(--orange)"/>
    <path d="M0 182 C110 170 230 228 340 222 S540 196 620 228 L620 238 C540 208 440 236 340 236 S120 186 0 196 Z" fill="var(--amber)"/>
  </svg>

  <div class="brand">
    <div class="brand__square"></div>
    <div class="brand__name">LANTERNFIELD</div>
    <div class="brand__sub">DRINKS</div>
  </div>

  <div class="person">
    <div class="person__name">Evan Marlowe Reed</div>
    <div class="person__title">Managing Director</div>
  </div>

  <ul class="contact">
    <li class="contact__item">555.214.3080
      <svg class="contact__icon" viewBox="0 0 16 16"><path d="M3 2h3l1 4-2 1c1 2 2 3 4 4l1-2 4 1v3c0 1-1 2-2 2C7 15 1 9 1 4c0-1 1-2 2-2z" fill="var(--white)"/></svg>
    </li>
    <li class="contact__item">555.867.1402
      <svg class="contact__icon" viewBox="0 0 16 16"><rect x="4" y="1" width="8" height="14" rx="1.5" fill="none" stroke="var(--white)" stroke-width="1.6"/><circle cx="8" cy="12.5" r="1" fill="var(--white)"/></svg>
    </li>
    <li class="contact__item">evan@lanternfielddrinks.com
      <svg class="contact__icon" viewBox="0 0 16 16"><rect x="1" y="3" width="14" height="10" fill="var(--white)"/><path d="M1 3l7 6 7-6" fill="none" stroke="var(--orange)" stroke-width="1.4"/></svg>
    </li>
    <li class="contact__item">www.lanternfielddrinks.com
      <svg class="contact__icon" viewBox="0 0 16 16"><g fill="none" stroke="var(--white)" stroke-width="1.3"><circle cx="8" cy="8" r="6.5"/><ellipse cx="8" cy="8" rx="3" ry="6.5"/><path d="M1.5 8h13M3 4.5h10M3 11.5h10"/></g></svg>
    </li>
    <li class="contact__item">48 Orchard Lane, Millbrook, US 10427
      <svg class="contact__icon" viewBox="0 0 16 16"><path d="M8 1a5 5 0 0 0-5 5c0 4 5 9 5 9s5-5 5-9a5 5 0 0 0-5-5z" fill="var(--white)"/><circle cx="8" cy="6" r="1.8" fill="var(--orange)"/></svg>
    </li>
  </ul>
</section>

</body>
</html>
```